Camp Thornbrook 2021 Magazine Design

We are for someone to design our annual magazine/newsletter. This is a print newsletter that is a total of 20 pages. It will need to be designed in a way that is easy to share with our printers. The designer will need to be someone who is creative and easy to work with.
For those interested in this project we ask that you design 4 to 6 pages for us to view. Once we select the designer we will want the rest created in a two-week time span. For those submitting a bid please include front cover, theme & dates, mission & vision, and Make the Difference.

This link will provide the layout of the newsletter https://files.parcelvault.example/doc/7qzRk2LmVt9XwPa4NbHc6DsYe3FuJg8KoTiW5rQx/edit?share=1.

This link will provide you with the pictures that are needed and a few documents https://files.parcelvault.example/folders/4TpWx8QnRb2ZyLc7MfVd5HsJ?share=1

Details:
20 pages long (including covers)
8.5 x 11

Please message me if you need any further details.

Target Market(s)

Our alumni base. Covers all ages

Requirements
Must have
• Spelled out in document
Nice to have
• Spelled out in document
Should not have
• Spelled out in document

```html
<!DOCTYPE html>
<html lang="en">
<head>
<meta charset="utf-8">
<title>Camp Thornbrook – Vision, Mission &amp; Core Values</title>
<link rel="stylesheet" href="https://fonts.googleapis.com/css2?family=Bebas+Neue&family=PT+Serif&display=swap">
<style>
  :root {
    --mint-bg: #e2f0ea;
    --sage-top: #9cc39a;
    --photo-warm: #8a8a5e;
    --vision-green: #9dd166;
    --mission-teal: #66c6b4;
    --values-yellow: #ffc452;
    --ink: #1f2421;
    --dot-line: #b6cdc5;
    --bullet-teal: #6aa89a;
    --bullet-orange: #ffb36b;
    --bullet-lime: #bfe08e;
    --band: #8dd0c0;
  }
  * { margin: 0; padding: 0; box-sizing: border-box; }
  html, body { width: 927px; height: 1200px; overflow: hidden; }
  body { background: var(--mint-bg); font-family: "PT Serif", Georgia, serif; color: var(--ink); }
  .page { position: relative; width: 927px; height: 1200px; overflow: hidden; }

  .hero-photo {
    position: absolute; left: 0; top: 0; width: 927px; height: 342px;
    background:
      radial-gradient(ellipse 330px 210px at 450px 250px, rgba(112,108,80,.75), rgba(112,108,80,0) 75%),
      linear-gradient(180deg, var(--sage-top) 0%, #b9c796 55%, var(--mint-bg) 100%);
  }

  .panel {
    position: absolute; left: 55px; width: 817px;
    border: 1px dotted var(--dot-line); border-radius: 14px;
  }
  .panel-vision { top: 391px; height: 170px; }
  .panel-mission { top: 555px; height: 160px; }
  .panel-values { top: 711px; height: 395px; }

  .section-head {
    position: absolute; left: 76px; width: 231px; height: 35px;
    display: flex; align-items: center; gap: 4px; padding-left: 7px;
    font-family: "Bebas Neue", "Oswald", sans-serif; font-size: 39px; line-height: 1; letter-spacing: .2px;
    padding-top: 4px;
  }
  .section-head svg { width: 30px; height: 30px; flex: none; margin-top: -4px; }
  .head-vision { top: 380px; background: var(--vision-green); }
  .head-mission { top: 537px; background: var(--mission-teal); }
  .head-values { top: 690px; background: var(--values-yellow); }

  .list { position: absolute; left: 100px; right: 60px; list-style: none; font-size: 16px; }
  .list li { position: relative; padding-left: 14px; }
  .list li::before {
    content: ""; position: absolute; left: 0; top: 7px; width: 7px; height: 7px; border-radius: 50%;
  }
  .vision-list { top: 423px; }
  .vision-list li { margin-bottom: 10px; }
  .vision-list li::before { background: var(--bullet-teal); }
  .mission-list { top: 584px; line-height: 25px; }
  .mission-list li::before { background: var(--bullet-orange); top: 9px; }
  .values-list { top: 743px; line-height: 20px; }
  .values-list li { margin-bottom: 17px; }
  .values-list li::before { background: var(--bullet-lime); }

  .bottom-band { position: absolute; left: 0; bottom: 0; width: 927px; height: 24px; background: var(--band); }
  .page-number {
    position: absolute; left: 891px; top: 1152px; width: 18px; height: 24px; background: var(--band);
    font-family: "Bebas Neue", sans-serif; font-size: 17px; text-align: center; line-height: 28px;
  }
</style>
</head>
<body>
<div class="page">
  <div class="hero-photo" role="img" aria-label="Four friends seen from behind with arms around each other, looking out over an open field at sunset"></div>

  <div class="panel panel-vision"></div>
  <div class="panel panel-mission"></div>
  <div class="panel panel-values"></div>

  <h2 class="section-head head-vision">
    <svg viewBox="0 0 30 30" aria-hidden="true">
      <path d="M2 15 Q15 3 28 15 Q15 27 2 15Z" fill="#fff"/>
      <circle cx="15" cy="15" r="5.5" fill="var(--vision-green)"/>
      <circle cx="15" cy="15" r="2.6" fill="#fff"/>
    </svg>
    Our Vision
  </h2>
  <ul class="list vision-list">
    <li>Encountering Christ</li>
    <li>Encountering Community</li>
    <li>Encountering Creation</li>
  </ul>

  <h2 class="section-head head-mission">
    <svg viewBox="0 0 30 30" aria-hidden="true">
      <path d="M17 2 C26 4 10 12 20 17 C28 21 22 27 16 29 L4 29 C12 26 14 22 8 18 C2 13 12 6 17 2Z" fill="#fff"/>
    </svg>
    Our Mission
  </h2>
  <ul class="list mission-list">
    <li>We want to strengthen young people’s relationship with Christ through meaningful worship experiences, create an environment that promotes community through Christ-centered relationships, and provide opportunities to experience God’s presence through His creation.</li>
  </ul>

  <h2 class="section-head head-values">
    <svg viewBox="0 0 30 30" aria-hidden="true">
      <circle cx="15" cy="15" r="12" fill="none" stroke="#fff" stroke-width="3"/>
      <circle cx="15" cy="15" r="6" fill="none" stroke="#fff" stroke-width="3"/>
      <circle cx="15" cy="15" r="2" fill="#fff"/>
    </svg>
    Core Values
  </h2>
  <ul class="list values-list">
    <li>We believe camp ministry to be a highly effective way to minister to young people.</li>
    <li>We teach Biblical truth in love.</li>
    <li>We provide leadership and ministry opportunities for our counselors and staff members.</li>
    <li>We believe that the summer camp experience provides opportunities for creating and strengthening lifelong Christ centered relationships.</li>
    <li>We believe that the glory of God can be seen and experienced through His creation in nature.</li>
    <li>We believe it is important to bring glory to God by being good stewards of the gifts given to the mission of Camp Thornbrook.</li>
    <li>We want to provide the best experience possible for a reasonable price.</li>
  </ul>

  <div class="page-number">17</div>
  <div class="bottom-band"></div>
</div>
</body>
</html>
```